Buch-/E-Book-Cover für Referenzbuch der Industrie
Zielgruppe
Als Manufaktur einzigartiger Fachmedien präsentiert verlag-technova Schlüsseltechnologien und ihre Märkte. Faszination für Technik ist die Grundlage unserer Arbeit. Mehr als 30 Jahre verlegerische Erfahrung und das Verständnis für Technologiemärkte machen uns zu einem anerkannten Partner der Industrie.
Unsere Medienmarken knüpfen ein starkes und weit verzweigtes Netzwerk – Print und digital – , in dem sich Anbieter und Anwender von Technologien und Produkten in ihren Zielsetzungen wiederfinden.
Unsere Magazine, Events und Netzwerkveranstaltungen sowie kundenspezifische Kommunikations- & Strategiekampagnen setzen in ihren Zielmärkten Maßstäbe und genießen bei Lesern, Kunden und Partnern Vertrauen und Respekt.
Für das ausgeschriebene Projekt handelt es sich um unsere Referenzpublikation MACHINA.ahead LUMEVETA.
LUMEVETA {polynesisch: Freiraum}
Das Referenzbuch der Industrie. Für Vorwärtsdenker und Zukunftsmacher.
Wandel bestimmt unsere Zeit und verändert unsere Gesellschaft, unsere Unternehmen, uns alle.
Im Wandel liegt Freiraum zur Gestaltung. Gesellschaftlicher Wandel, Technologie-Wandel, Klimawandel, Wertewandel, Führungswandel oder Organisationswandel sind nur einige Beispiele. Wer dabei den Wandel in engen Bahnen denkt, verschenkt Potential. Veränderung braucht Freiraum für neue Ideen und Perspektiven sowie Persönlichkeiten, die diesen nutzen wollen.
Aber wer gestaltet die Zukunft der Industrie und ihrer Branchen? Und wie?
Wir geben Personen aus der Industrie den Freiraum, ihre Perspektiven auf und aus dem Wandel zu erzählen. Warum? Weil sie uns begeistert haben, in persönlichen Treffen und Gesprächen, durch streitbare Meinungen und ehrliche Geschichten. Weil sie die Zukunft verändern.
LUMEVETA ist eine Aufforderung: Zum Mitdenken, Weiterdenken, aber auch Nachdenken.
LUMEVETA – RAUM FÜR NEUES
Ein Referenzbuch, d..
Aufgabenstellung
1. Kurzzusammenfassung der Ausschreibung
Die 4. Ausgabe des jährlichen Referenzbuchs der Industrie, MACHINA.ahead LUMEVETA 2025, erscheint im Oktober 2024. Für das Cover sucht der verlag-technova Verlag neue Vorschläge, die die Themen Freiraum und Wandel in den Fokus stellen.
2. Gestalterische & Inhaltliche Anforderungen
• Format: 195x250 mm + Anschnitt
• Rücken: ca. 1,6 cm (Stand letzte Publikation 2023)
• Auflösung: Druckqualität, mind. 300 dpi
• Inhaltliche Elemente:
- LUMEVETA Schriftzug
- {polynesisch: Freiraum}
- Untersatz: Das Referenzbuch der Industrie. Für Vorwärtsdenker und Zukunftsmacher.
- part of MACHINA.ahead Logo-Balken am unteren Rand (siehe Beispiel AuD_Titelbeispiel_Logobalken)
WICHTIG: Der aktuelle Schriftzug LUMEVETA und die Farbe Orange (0/80/100/0) (siehe Beispiel LUMEVETA 2021) sollen als Wiedererkennung in die Gestaltungen eingebunden werden.

```html
<!DOCTYPE html>
<html lang="de">
<head>
<meta charset="utf-8">
<title>MACHINA.ahead LUMEVETA 2025 – Cover</title>
<link rel="stylesheet" href="https://fonts.googleapis.com/css2?family=Bebas+Neue&family=Roboto:wght@400&display=swap">
<style>
  :root {
    --orange: #cc5a2a;
    --paper: #ffffff;
    --ink: #111111;
    --backdrop: #efe9dd;
  }
  * { margin: 0; padding: 0; box-sizing: border-box; }
  html, body {
    width: 849px;
    height: 1200px;
    overflow: hidden;
    background: var(--backdrop);
  }
  .cover-spread {
    position: absolute;
    left: 20px;
    top: 349px;
    width: 809px;
    height: 502px;
    background: var(--paper);
    box-shadow: 0 4px 10px rgba(0,0,0,0.25);
    overflow: hidden;
  }
  .rule {
    position: absolute;
    height: 3px;
    background: var(--orange);
  }
  .back-rule-upper { left: 0; width: 262px; top: 199px; }
  .back-rule-lower { left: 0; width: 262px; top: 435px; }
  .spine {
    position: absolute;
    left: 262px;
    top: 0;
    width: 170px;
    height: 100%;
    background: var(--orange);
  }
  .front-rule-top { left: 432px; right: 0; top: 30px; }
  .front-rule-year { left: 546px; width: 171px; top: 202px; }
  .front-rule-bottom { left: 546px; right: 0; top: 430px; }

  .emblem {
    position: absolute;
    left: 313px;
    top: 159px;
    width: 152px;
    height: 192px;
    border-radius: 50% 50% 50% 50% / 40% 40% 60% 60%;
    background: radial-gradient(circle at 45% 60%, #f2f2f2 0%, #555 35%, #111 70%);
  }

  .title-stack {
    position: absolute;
    left: 436px;
    top: 0;
    z-index: 2;
    font-family: "Bebas Neue", sans-serif;
    font-weight: 400;
    color: var(--orange);
    font-size: 142px;
    line-height: 1;
    letter-spacing: -2px;
  }
  .title-syllable {
    position: absolute;
    left: 0;
    white-space: nowrap;
    transform: scaleX(0.86);
    transform-origin: left top;
  }
  .syl-1 { top: 26px; }
  .syl-2 { top: 132px; }
  .syl-3 { top: 252px; }
  .syl-4 { top: 360px; }

  .head-industry {
    position: absolute;
    left: 556px;
    top: 54px;
    width: 100px;
    height: 148px;
    border-radius: 45% 45% 10% 10%;
    background: linear-gradient(180deg, #8a8a8a 0%, #1a1a1a 55%, #111 100%);
  }
  .head-nature {
    position: absolute;
    left: 629px;
    top: 282px;
    width: 109px;
    height: 146px;
    border-radius: 45% 45% 10% 10%;
    background: linear-gradient(180deg, #7d7d7d 0%, #1a1a1a 55%, #111 100%);
  }

  .edition-year {
    position: absolute;
    left: 665px;
    top: 174px;
    font-family: "Roboto", sans-serif;
    font-size: 23px;
    line-height: 28px;
    color: var(--ink);
  }
  .subtitle {
    position: absolute;
    left: 583px;
    top: 211px;
    font-family: "Roboto", sans-serif;
    font-size: 12px;
    line-height: 16px;
    color: var(--ink);
  }
  .imprint {
    position: absolute;
    left: 622px;
    top: 450px;
    font-family: "Roboto", sans-serif;
    font-weight: 400;
    font-size: 14px;
    line-height: 18px;
    color: var(--ink);
    white-space: nowrap;
  }
</style>
</head>
<body>
  <main class="cover-spread">
    <div class="rule back-rule-upper"></div>
    <div class="rule back-rule-lower"></div>

    <div class="spine"></div>

    <div class="rule front-rule-top"></div>

    <div class="emblem" role="img" aria-label="Schwarz-weiße Spiral-Illustration mit Pfeilen und Dreieck über dem Buchrücken"></div>

    <h1 class="title-stack" aria-label="LUMEVETA">
      <span class="title-syllable syl-1">LU</span>
      <span class="title-syllable syl-2">ME</span>
      <span class="title-syllable syl-3">VE</span>
      <span class="title-syllable syl-4">TA</span>
    </h1>

    <div class="head-industry" role="img" aria-label="Silhouetten-Illustration eines Kopfes voller Zahnräder, Globus und Aufwärtspfeile"></div>
    <div class="head-nature" role="img" aria-label="Silhouetten-Illustration eines Kopfes mit Wald, Windrädern und Stadt"></div>

    <p class="edition-year">2025</p>
    <div class="rule front-rule-year"></div>
    <p class="subtitle">LUMEVETA Das Referenzbuch<br>der Industrie.<br>Für Vorwärtsdenker<br>und Zukunftsmacher.</p>

    <div class="rule front-rule-bottom"></div>
    <p class="imprint">part of MACHINA.ahead</p>
  </main>
</body>
</html>
```